Education Offering Flyer

Design a simple and clean A4 flyer, front and back, that presents our sales offering in an attractive way. The flyer consists of a title, a sub-heading, bullet points, paragraphed content and a small diagram with a caption.The design needs to be consistent with the style of the PowerPoint presentation that is attached.

We are a company that provides education software solutions for districts, schools, teachers, and students. We have a portfolio of products and services. Our offerings combine our products and services in different ways to address different education needs.

The target audience of this flyer is a decision-maker in an education organization.

Specifications:

Design a double-sided A4 flyer
Maintain our corporate logo color theme and tones (orange, blue, green, white, grey)
Follow PPTX style/theme (fonts, circles, squares, boxes)
Deliver a professional (business), clean, and modern look
Use photos that are relevant e.g. school and students with devices and technology [Optional]
Include icons [Optional]

I would like to receive the final file as a PSD format for hard copy printing. But for the purpose of review, a JPEG would be suitable.

```html
<!DOCTYPE html>
<html lang="en">
<head>
<meta charset="utf-8">
<title>Brightpath Learning – LMS Offering Flyer</title>
<link rel="stylesheet" href="https://fonts.googleapis.com/css2?family=Arimo:wght@400;700&display=swap">
<style>
  :root {
    --cyan: #3ccfd6;
    --red: #f0452a;
    --orange: #f7a23f;
    --green: #8ed93a;
    --lms-green: #7ed321;
    --ink: #111111;
    --grey-arrow: #9aa3a8;
    --paper: #ffffff;
    --wash: #eef5ec;
  }
  * { box-sizing: border-box; margin: 0; padding: 0; }
  html, body { width: 848px; height: 1200px; overflow: hidden; }
  body {
    font-family: "Arimo", Arial, sans-serif;
    color: var(--ink);
    background: var(--paper);
  }
  .flyer {
    position: relative;
    width: 848px;
    height: 1200px;
    overflow: hidden;
    background: linear-gradient(160deg, var(--wash) 0%, #f7faf5 35%, var(--paper) 60%);
  }

  /* Offering rows */
  .offer-badge {
    position: absolute; left: 40px;
    width: 128px; height: 128px; border-radius: 50%;
    display: flex; align-items: center; justify-content: center;
    color: var(--paper); font-weight: 700; font-size: 16px;
  }
  .offer-text {
    position: absolute; left: 201px;
    font-size: 15px; line-height: 17.5px; white-space: nowrap;
  }
  .badge-why { top: 43px; background: var(--cyan); }
  .badge-who { top: 180px; background: var(--red); }
  .badge-what { top: 318px; background: var(--orange); }
  .badge-aspects { top: 462px; background: var(--green); }
  .text-why { top: 56px; }
  .text-who { top: 220px; }
  .text-what { top: 357px; }
  .text-aspects { top: 488px; }

  /* Diagram */
  .order-title {
    position: absolute; left: 574px; top: 62px; width: 180px;
    text-align: center; font-weight: 700; font-size: 23px; line-height: 1.1;
  }
  .diagram { position: absolute; left: 500px; top: 140px; width: 320px; height: 300px; }
  .node { position: absolute; color: var(--orange); font-weight: 700; font-size: 16px; text-align: center; line-height: 1.15; }
  .node-tools { left: 78px; top: 10px; width: 160px; }
  .node-lcms { left: 4px; top: 122px; width: 60px; }
  .node-sms { left: 260px; top: 122px; width: 50px; }
  .node-site { left: 108px; top: 264px; width: 100px; }
  .node-lms { left: 98px; top: 140px; width: 120px; color: var(--lms-green); font-size: 42px; }
  .diagram-arrows { position: absolute; left: 0; top: 0; }

  /* Lower left */
  .section-title { position: absolute; left: 60px; font-weight: 700; font-size: 23px; }
  .section-body { position: absolute; left: 60px; font-size: 16px; line-height: 22px; white-space: nowrap; }
  .integration-title { top: 728px; }
  .integration-body { top: 772px; }
  .dependencies-title { top: 972px; }
  .dependencies-body { top: 1012px; }

  /* Artwork */
  .artwork { position: absolute; left: 250px; top: 470px; width: 598px; height: 730px; }

  /* Brand */
  .brand { position: absolute; left: 606px; top: 934px; display: flex; align-items: center; gap: 8px; }
  .brand-dot { width: 20px; height: 20px; border-radius: 50%; background: var(--orange); }
  .brand-name { font-weight: 700; font-size: 20px; color: var(--orange); white-space: nowrap; }
  .brand-url { position: absolute; left: 625px; top: 996px; font-size: 15px; }
  .brand-tagline { position: absolute; left: 625px; top: 1030px; width: 200px; font-size: 11px; line-height: 1.2; }
</style>
</head>
<body>
<main class="flyer">

  <div class="offer-badge badge-why">Why</div>
  <p class="offer-text text-why">A unified system for digital work<br>exchange that provides students and<br>teachers with a single, easy, and<br>dependable solution to manage<br>academic and administrative needs.</p>

  <div class="offer-badge badge-who">Who</div>
  <p class="offer-text text-who">K-12 schools, network<br>of schools, districts,<br>and states.</p>

  <div class="offer-badge badge-what">What</div>
  <p class="offer-text text-what">Manage teaching and<br>learning workflows.</p>

  <div class="offer-badge badge-aspects">Aspects</div>
  <p class="offer-text text-aspects">Assignments, Lesson Planning, Individual<br>Learning Plan, Gradebook, Assessments, Behavior, Attendance,<br>Content Library, Virtual Classes, e-Portfolio, Calendar, Communication<br>&amp; Collaboration, Parent Portal, and Administration.</p>

  <h2 class="order-title">BRINGING<br>ORDER</h2>
  <div class="diagram">
    <svg class="diagram-arrows" width="320" height="300" viewBox="0 0 320 300" aria-hidden="true">
      <defs>
        <marker id="arrowhead" markerWidth="8" markerHeight="8" refX="6" refY="4" orient="auto">
          <path d="M0,0 L7,4 L0,8 Z" fill="#9aa3a8"/>
        </marker>
      </defs>
      <g stroke="#9aa3a8" stroke-width="1.4" fill="none" marker-end="url(#arrowhead)">
        <line x1="158" y1="66" x2="158" y2="130"/>
        <line x1="60" y1="144" x2="98" y2="162"/>
        <line x1="264" y1="144" x2="222" y2="162"/>
        <line x1="158" y1="200" x2="158" y2="256"/>
      </g>
    </svg>
    <div class="node node-tools">Other Tools<br>Systems e.g.<br>plagiarism</div>
    <div class="node node-lcms">LCMS</div>
    <div class="node node-sms">SMS</div>
    <div class="node node-lms">LMS</div>
    <div class="node node-site">Website</div>
  </div>

  <h2 class="section-title integration-title">Integration</h2>
  <p class="section-body integration-body">Third-party SMS/SIS,<br>content management<br>systems, or other tools<br>and systems, school<br>or university websites<br>or portals.</p>
  <h2 class="section-title dependencies-title">Dependencies</h2>
  <p class="section-body dependencies-body">None.</p>

  <svg class="artwork" role="img" aria-label="Colourful paint splash with bright leaves in orange, purple, green, pink and blue" viewBox="0 0 598 730">
    <defs>
      <radialGradient id="splash" cx="0.62" cy="0.68" r="0.75">
        <stop offset="0" stop-color="#ffffff"/>
        <stop offset="0.18" stop-color="#ffffff"/>
        <stop offset="0.38" stop-color="#9fd8f0"/>
        <stop offset="0.55" stop-color="#6a4fd8"/>
        <stop offset="0.72" stop-color="#f28a1e"/>
        <stop offset="0.88" stop-color="#e6207a"/>
        <stop offset="1" stop-color="#7cc63a"/>
      </radialGradient>
    </defs>
    <path d="M598,0 C520,20 470,90 420,80 C340,70 300,140 240,170 C160,210 60,240 40,330 C20,420 0,520 30,610 C50,680 40,730 40,730 L598,730 Z" fill="url(#splash)"/>
  </svg>

  <div class="brand">
    <span class="brand-dot"></span>
    <span class="brand-name">Brightpath Learning</span>
  </div>
  <p class="brand-url">www.brightpath.education</p>
  <p class="brand-tagline">Brightpath Learning - Addressing the needs of K-12 institutions worldwide.</p>

</main>
</body>
</html>
```